Redesign of business card for Cedar Ridge Mechanical

We are looking for a new design for our business cards for Cedar Ridge Mechanical. We are a plumbing & HVAC construction company, operating on the West Coast of Canada and USA. Logo attached.
Industry/Entity Type
Construction - Plumbing & HVAC
Contact Information for Business Card
Name, address, phone numbers, email, website address
Look and feel
Each slider illustrates characteristics of the customer's brand and the style your logo design should communicate.

```html
<!DOCTYPE html>
<html lang="en">
<head>
<meta charset="utf-8">
<title>Cedar Ridge Mechanical — Business Card</title>
<link rel="stylesheet" href="https://fonts.googleapis.com/css2?family=Poppins:wght@400;500;700&display=swap">
<style>
  :root {
    --backdrop: #232323;
    --card: #e6e7e7;
    --card-back: #e4e5e5;
    --ink: #111111;
    --ink-soft: #1c1c1c;
    --faint: #d2d3d3;
    --emboss: #cfd0d0;
  }
  * { box-sizing: border-box; margin: 0; padding: 0; }
  html, body { width: 1200px; height: 780px; overflow: hidden; }
  body {
    background: var(--backdrop);
    font-family: "Poppins", sans-serif;
    color: var(--ink);
    position: relative;
  }
  .card { position: absolute; background: var(--card); border-radius: 3px; }

  /* Front (portrait) */
  .card-front { left: 110px; top: 80px; width: 360px; height: 620px; overflow: hidden; }
  .front-decoration {
    position: absolute; left: 0; top: 0; width: 100%; height: 290px;
  }
  .front-brand {
    position: absolute; left: 34px; top: 318px;
    display: flex; align-items: center; gap: 12px;
  }
  .brand-square { width: 26px; height: 26px; background: var(--ink); flex: none; }
  .brand-name {
    font-weight: 700; font-size: 19px; line-height: 1.15; color: var(--ink);
    text-transform: uppercase; letter-spacing: 0.5px;
  }
  .person { position: absolute; left: 0; top: 404px; padding-left: 34px; }
  .person::before {
    content: ""; position: absolute; left: 0; top: 4px; width: 20px; height: 64px;
    background: var(--ink);
  }
  .person-name { font-size: 26px; line-height: 1.15; }
  .person-name .first { font-weight: 700; }
  .person-name .last { font-weight: 400; }
  .person-title { font-size: 14px; font-weight: 500; margin-top: 2px; }
  .address { position: absolute; left: 34px; top: 488px; font-size: 13px; line-height: 1.45; }
  .contact-list { position: absolute; left: 34px; top: 534px; list-style: none; font-size: 13px; line-height: 1.55; }
  .contact-list li { display: flex; align-items: center; gap: 8px; }
  .contact-list svg { width: 13px; height: 13px; flex: none; fill: var(--ink-soft); }

  /* Back (landscape) */
  .card-back { left: 520px; top: 200px; width: 600px; height: 380px; background: var(--card-back); }
  .back-brand {
    position: absolute; left: 0; right: 0; top: 50%; transform: translateY(-50%);
    display: flex; align-items: center; justify-content: center; gap: 16px;
  }
  .back-brand .brand-square { width: 40px; height: 40px; background: var(--emboss); }
  .back-brand .brand-name { font-size: 28px; color: var(--emboss); }
</style>
</head>
<body>
  <section class="card card-front" aria-label="Business card front">
    <svg class="front-decoration" viewBox="0 0 360 290" aria-hidden="true">
      <rect x="0" y="0" width="360" height="290" fill="var(--card)"/>
      <rect x="150" y="40" width="170" height="170" rx="18" fill="none" stroke="var(--faint)" stroke-width="26"/>
    </svg>

    <div class="front-brand">
      <span class="brand-square"></span>
      <span class="brand-name">Cedar Ridge<br>Mechanical</span>
    </div>

    <div class="person">
      <p class="person-name"><span class="first">Maren</span> <span class="last">Holloway</span></p>
      <p class="person-title">Founder &amp; CEO</p>
    </div>

    <p class="address">418 Harbor Ln. Suite 120<br>Tacoma, WA 98402</p>

    <ul class="contact-list">
      <li>
        <svg viewBox="0 0 24 24" aria-hidden="true"><path d="M6.6 10.8a15 15 0 0 0 6.6 6.6l2.2-2.2c.3-.3.7-.4 1-.2 1.1.4 2.3.6 3.6.6.6 0 1 .4 1 1V20c0 .6-.4 1-1 1A17 17 0 0 1 3 4c0-.6.4-1 1-1h3.5c.6 0 1 .4 1 1 0 1.3.2 2.5.6 3.6.1.3 0 .7-.2 1z"/></svg>
        <span>(253) 555-0147</span>
      </li>
      <li>
        <svg viewBox="0 0 24 24" aria-hidden="true"><path d="M2 5h20v14H2zm2 2v.5l8 5 8-5V7zm0 2.8V17h16V9.8l-8 5z"/></svg>
        <span>info@yourwebsite.com</span>
      </li>
      <li>
        <svg viewBox="0 0 24 24" aria-hidden="true"><path d="M12 2a10 10 0 1 0 0 20 10 10 0 0 0 0-20zm6.9 6h-3a15 15 0 0 0-1.3-3.9A8 8 0 0 1 18.9 8zM12 4c.8 1.2 1.5 2.5 1.9 4h-3.8c.4-1.5 1.1-2.8 1.9-4zM4.3 14a8 8 0 0 1 0-4h3.4a16 16 0 0 0 0 4zm.8 2h3a15 15 0 0 0 1.3 3.9A8 8 0 0 1 5.1 16zm3-8h-3a8 8 0 0 1 4.3-3.9C8.8 5.3 8.4 6.6 8.1 8zM12 20c-.8-1.2-1.5-2.5-1.9-4h3.8c-.4 1.5-1.1 2.8-1.9 4zm2.3-6H9.7a14 14 0 0 1 0-4h4.6a14 14 0 0 1 0 4zm.3 5.9c.6-1.2 1-2.5 1.3-3.9h3a8 8 0 0 1-4.3 3.9zm1.7-5.9a16 16 0 0 0 0-4h3.4a8 8 0 0 1 0 4z"/></svg>
        <span>www.yourwebsite.com</span>
      </li>
    </ul>
  </section>

  <section class="card card-back" aria-label="Business card back">
    <div class="back-brand">
      <span class="brand-square"></span>
      <span class="brand-name">Cedar Ridge Mechanical</span>
    </div>
  </section>
</body>
</html>
```